Corporate Business Card

Very professional, Modern, Not to busy, include phone address email, website
(253) 617-4930, 18761 52nd Avenue S, Kent, WA 98047, martin@plumlinegroup.com, varkoworks.com

Target Market(s)

Manufacturing

Industry/Entity Type

Aero, machining, manufacturing, Off road racing

Contact Information for Business Card

Phone, address email, website

```html
<!DOCTYPE html>
<html lang="en">
<head>
<meta charset="utf-8">
<title>Varko Works – Business Card</title>
<link rel="stylesheet" href="https://fonts.googleapis.com/css2?family=Montserrat:wght@400;500;700&display=swap">
<style>
  :root {
    --navy: #17386f;
    --red: #d8262e;
    --white: #ffffff;
    --silver: #c9cbd0;
    --ink: #1b1b1f;
    --backdrop: #2b2b2e;
  }
  * { margin: 0; padding: 0; box-sizing: border-box; }
  html, body { width: 1200px; height: 1015px; overflow: hidden; }
  body {
    background: var(--backdrop);
    font-family: "Montserrat", sans-serif;
    position: relative;
  }
  .card {
    position: absolute;
    left: 320px;
    width: 560px;
    height: 320px;
    overflow: hidden;
    box-shadow: 0 10px 30px rgba(0,0,0,.45);
  }
  .card--front { top: 110px; background: var(--navy); }
  .card--back { top: 585px; background: var(--white); }

  .brand {
    position: absolute;
    display: flex;
    flex-direction: column;
    align-items: flex-end;
  }
  .brand__name {
    font-weight: 700;
    letter-spacing: 2px;
    line-height: 1;
  }
  .brand__rule { height: 2px; margin-top: 10px; }

  .card--front .brand { left: 0; right: 0; top: 112px; align-items: center; }
  .card--front .brand__name { font-size: 58px; color: var(--silver); }
  .card--front .brand__rule { width: 300px; background: var(--silver); }

  .card--back .brand { right: 40px; top: 42px; }
  .card--back .brand__name { font-size: 38px; color: var(--navy); }
  .card--back .brand__rule { width: 210px; background: var(--navy); }

  .address {
    position: absolute;
    left: 40px;
    top: 130px;
    font-size: 13px;
    line-height: 1.45;
    color: var(--ink);
  }
  .contact {
    position: absolute;
    left: 40px;
    top: 196px;
    list-style: none;
    font-size: 12.5px;
    color: var(--ink);
  }
  .contact li { display: flex; align-items: center; gap: 9px; height: 19px; }
  .contact svg { width: 12px; height: 12px; fill: var(--red); flex: none; }

  .wave { position: absolute; inset: 0; width: 560px; height: 320px; }
  .wave__band { fill: var(--navy); }
  .wave__stripe { fill: var(--red); }
</style>
</head>
<body>

<section class="card card--front" aria-label="Card front">
  <div class="brand">
    <span class="brand__name">VARKO WORKS</span>
    <span class="brand__rule"></span>
  </div>
</section>

<section class="card card--back" aria-label="Card back">
  <svg class="wave" viewBox="0 0 560 320" aria-hidden="true">
    <path class="wave__band" d="M0,320 L0,300 C150,296 255,238 338,178 C402,132 470,116 560,112 L560,320 Z"/>
    <path class="wave__stripe" d="M20,292 C175,282 268,218 348,162 C410,120 478,104 548,96 C478,110 414,132 356,172 C276,228 176,288 20,292 Z"/>
  </svg>

  <div class="brand">
    <span class="brand__name">VARKO WORKS</span>
    <span class="brand__rule"></span>
  </div>

  <p class="address">18761 52nd Avenue<br>S, Kent, WA 98047</p>

  <ul class="contact">
    <li>
      <svg viewBox="0 0 24 24"><path d="M6.6 10.8a15.2 15.2 0 0 0 6.6 6.6l2.2-2.2a1 1 0 0 1 1-.25 11.4 11.4 0 0 0 3.6.57 1 1 0 0 1 1 1V20a1 1 0 0 1-1 1A17 17 0 0 1 3 4a1 1 0 0 1 1-1h3.5a1 1 0 0 1 1 1c0 1.25.2 2.45.57 3.57a1 1 0 0 1-.25 1z"/></svg>
      (253) 617-4930
    </li>
    <li>
      <svg viewBox="0 0 24 24"><path d="M2 5h20v14H2z M2 5l10 8 10-8" fill="none" stroke="#d8262e" stroke-width="2.4"/></svg>
      martin@plumlinegroup.com
    </li>
    <li>
      <svg viewBox="0 0 24 24"><circle cx="12" cy="12" r="10" fill="none" stroke="#d8262e" stroke-width="2.4"/><path d="M2 12h20M12 2c3 3 3 17 0 20M12 2c-3 3-3 17 0 20" fill="none" stroke="#d8262e" stroke-width="1.8"/></svg>
      www.varkoworks.com
    </li>
  </ul>
</section>

</body>
</html>
```